Mosquito and outdoor pest management

The uploaded logo must be integrated as the main theme of the card. I would like it to be modern and eye catching. Maybe some backround images or light silver metallic background.
Space enough at the base for contact info to be put in- phone numbers,emails,names,website.
Space on the back for short blog and lines for hand writing..calling card.
Commercial- golf courses, schools, outdoor function properties, pre event treatments.
Residential- retirement villages, townhome complexes and general houses
Management

```html
<!DOCTYPE html>
<html lang="en">
<head>
<meta charset="utf-8">
<title>Bayline Mosquito – Business Card</title>
<link href="https://fonts.googleapis.com/css2?family=Noto+Serif:wght@700&family=Open+Sans:wght@400&display=swap" rel="stylesheet">
<style>
  :root {
    --stage: #e6e4e1;
    --paper: #ffffff;
    --ink: #151515;
    --brand-red: #d8222f;
    --rule: #9a9a9a;
    --muted: #3a3a3a;
  }
  html, body {
    margin: 0;
    padding: 0;
    width: 1200px;
    height: 902px;
    overflow: hidden;
    background: var(--stage);
  }
  .canvas {
    width: 1200px;
    height: 902px;
    display: flex;
    flex-direction: column;
    align-items: center;
    justify-content: center;
    gap: 34px;
  }
  .card {
    position: relative;
    width: 700px;
    height: 400px;
    background: var(--paper);
    box-shadow: 0 6px 18px rgba(0,0,0,0.18);
    overflow: hidden;
  }
  .brand {
    position: absolute;
    display: flex;
    align-items: center;
    gap: 12px;
    font-family: "Noto Serif", serif;
    font-weight: 700;
    color: var(--ink);
    line-height: 1.05;
  }
  .brand-dot {
    width: 22px;
    height: 22px;
    border-radius: 50%;
    background: var(--brand-red);
    flex: none;
  }
  .brand-name { font-size: 30px; letter-spacing: 0.5px; }
  .brand-name small { display: block; font-size: 15px; letter-spacing: 1.5px; margin-top: 4px; }

  /* Front */
  .front .brand { left: 50px; top: 70px; }
  .swoosh { position: absolute; inset: 0; }
  .contact {
    position: absolute;
    right: 40px;
    top: 190px;
    text-align: right;
    font-family: "Open Sans", sans-serif;
    color: #fff;
  }
  .contact-name {
    font-family: "Noto Serif", serif;
    font-weight: 700;
    color: var(--brand-red);
    font-size: 30px;
    margin-bottom: 18px;
  }
  .contact-line {
    display: flex;
    justify-content: flex-end;
    align-items: center;
    gap: 12px;
    font-size: 18px;
    margin-bottom: 12px;
  }
  .contact-icon { width: 16px; height: 16px; flex: none; }

  /* Back */
  .back .brand { left: 50px; top: 48px; }
  .divider {
    position: absolute;
    left: 0; right: 0;
    top: 150px;
    height: 1px;
    background: var(--rule);
  }
  .service-col {
    position: absolute;
    top: 175px;
    font-family: "Open Sans", sans-serif;
  }
  .service-col.commercial { left: 50px; }
  .service-col.residential { left: 390px; }
  .service-col h2 {
    margin: 0 0 12px;
    font-family: "Noto Serif", serif;
    font-weight: 700;
    color: var(--brand-red);
    font-size: 30px;
  }
  .service-col ul { list-style: none; margin: 0; padding: 0; }
  .service-col li {
    font-size: 19px;
    color: var(--muted);
    margin-bottom: 6px;
  }
  .service-col li::before {
    content: "*";
    color: var(--brand-red);
    font-weight: 700;
    margin-right: 14px;
  }
</style>
</head>
<body>
<main class="canvas">

  <section class="card back" aria-label="Card back">
    <div class="brand">
      <span class="brand-dot"></span>
      <span class="brand-name">Bayline Mosquito<small>&amp; Outdoor Pest Care</small></span>
    </div>
    <div class="divider"></div>
    <div class="service-col commercial">
      <h2>Commercial</h2>
      <ul>
        <li>golf courses</li>
        <li>schools</li>
        <li>outdoor function properties</li>
        <li>pre event treatments</li>
      </ul>
    </div>
    <div class="service-col residential">
      <h2>Residential</h2>
      <ul>
        <li>retirement villages</li>
        <li>townhome complexes</li>
        <li>general houses</li>
      </ul>
    </div>
  </section>

  <section class="card front" aria-label="Card front">
    <svg class="swoosh" viewBox="0 0 700 400" preserveAspectRatio="none" aria-hidden="true">
      <path d="M190 400 C 235 190, 410 95, 700 25 L700 50 C 420 110, 250 200, 210 400 Z" fill="var(--brand-red)"/>
      <path d="M210 400 C 250 200, 420 110, 700 50 L700 400 Z" fill="var(--ink)"/>
    </svg>
    <div class="brand">
      <span class="brand-dot"></span>
      <span class="brand-name">Bayline Mosquito<small>&amp; Outdoor Pest Care</small></span>
    </div>
    <div class="contact">
      <div class="contact-name">Marcus Whitfield</div>
      <div class="contact-line">+1 555 014 2286
        <svg class="contact-icon" viewBox="0 0 16 16" aria-hidden="true"><rect width="16" height="16" fill="var(--brand-red)"/><path d="M5 3.5l1.6 2.2-1 1.1a6 6 0 0 0 3.6 3.6l1.1-1 2.2 1.6-.9 1.6C8 12.6 3.4 8 3.4 4.4z" fill="#fff"/></svg>
      </div>
      <div class="contact-line">hello@baylinepest.com
        <svg class="contact-icon" viewBox="0 0 16 16" aria-hidden="true"><rect width="16" height="16" fill="var(--brand-red)"/><rect x="3" y="4.5" width="10" height="7" fill="none" stroke="#fff" stroke-width="1.2"/><path d="M3 4.5l5 4 5-4" fill="none" stroke="#fff" stroke-width="1.2"/></svg>
      </div>
      <div class="contact-line">www.baylinepest.com
        <svg class="contact-icon" viewBox="0 0 16 16" aria-hidden="true"><rect width="16" height="16" fill="var(--brand-red)"/><circle cx="8" cy="8" r="4.6" fill="none" stroke="#fff" stroke-width="1.2"/><path d="M3.4 8h9.2M8 3.4c-2 2.6-2 6.6 0 9.2M8 3.4c2 2.6 2 6.6 0 9.2" fill="none" stroke="#fff" stroke-width="1"/></svg>
      </div>
    </div>
  </section>

</main>
</body>
</html>
```